West Australian based aspiring best selling novelist needs a book cover design

I have a completed manuscript for a fiction novel about 3 women whose partners work away in fly in fly out (FIFO) jobs. One woman has three young kids (boy, 8, boy 6 and girl 18months old), one woman is the first woman's sister and is young and beautiful but a bit troubled and one woman works on reception at a strip club. All three want to be independent but still miss their lovers. Location is the Midwest of Western Australia where there are beautiful beaches, blue skies and crayfish. The title is 'Salt Wind Over The Quiet Harbour.' Author's name is Lena Dorsk. I need a book cover design. I am unsure whether to try and capture the spirit of those women or the landscape or do a simple graphic design like crosses on a dateless calendar, counting down the days (Two weeks crossed off then one happy week when the lover is home and then another two sad weeks). The final design should lure people in to want to read the text. Thank you

Target Market(s)
Women, particularly those who are struggling with being a stay at home lover.

Must Have:
- Soul, an understanding of the complexity of loneliness. The women are strong and interesting- not flaky. This is NOT a romance novel. It is a quirky story with heart.

Nice to Have:
- A design that is striking but not too busy

Should Not Have:
- No trashy images of women. Should NOT look like a romance novel.

Target Market(s)

Women 18 upwards

Industry/Entity Type

Book Publisher

Font styles to use
Other font styles liked:
• unsure

Requirements
Must have
• A bit of quirkiness, soul, loneliness, independence
Nice to have
• Something striking but not too busy. I trust your skills!
Should not have
• Not look like a romance novel. The genre is more contemporary chick literature

```html
<!DOCTYPE html>
<html lang="en">
<head>
<meta charset="utf-8">
<title>Salt Wind Over The Quiet Harbour — Lena Dorsk</title>
<link href="https://fonts.googleapis.com/css2?family=League+Spartan:wght@600;700&family=Bitter:ital,wght@1,500&display=swap" rel="stylesheet">
<style>
  :root {
    --page-bg: #f3f3f3;
    --sky-top: #86acd6;
    --sky-mid: #c9dcee;
    --haze: #f4f2ef;
    --figure-warm: #b9774e;
    --figure-olive: #8f8a5e;
    --title-red: #b3141d;
    --ring-red: #e3151c;
    --ink: #111111;
  }
  * { margin: 0; padding: 0; box-sizing: border-box; }
  html, body {
    width: 1200px; height: 1200px; overflow: hidden;
    background: var(--page-bg);
  }
  .book-cover {
    position: absolute; left: 200px; top: 0;
    width: 800px; height: 1200px; overflow: hidden;
    background: var(--haze);
  }
  .cover-photo {
    position: absolute; inset: 0;
    background: linear-gradient(180deg, var(--sky-top) 0%, var(--sky-mid) 28%, #e9eef3 50%, var(--haze) 68%, #f7f6f4 100%);
  }
  .figure-area {
    position: absolute; left: 7px; top: 437px; width: 482px; height: 763px;
    border-radius: 45% 45% 0 0 / 28% 28% 0 0;
    background: linear-gradient(180deg, #c99a63 0%, var(--figure-warm) 38%, var(--figure-olive) 70%, #7d7a52 100%);
    opacity: 0.9;
  }
  .title-small, .title-tail {
    position: absolute;
    font-family: "League Spartan", sans-serif;
    font-weight: 700; color: var(--ink);
    font-size: 66px; line-height: 1; letter-spacing: 1px;
  }
  .title-small { left: 32px; top: 72px; }
  .title-tail { right: 28px; top: 478px; text-align: right; }
  .title-feature {
    position: absolute; left: 0; width: 800px; text-align: center;
    font-family: "League Spartan", sans-serif;
    font-weight: 700; color: var(--title-red);
    font-size: 158px; line-height: 1; letter-spacing: 2px;
    opacity: 0.92;
  }
  .title-feature.line-one { top: 152px; }
  .title-feature.line-two { top: 292px; }
  .date-ring {
    position: absolute; left: 0; top: 0; width: 800px; height: 600px;
  }
  .author-name {
    position: absolute; right: 28px; top: 1098px;
    font-family: "Bitter", serif; font-style: italic; font-weight: 500;
    font-size: 68px; line-height: 1; color: var(--ink);
  }
</style>
</head>
<body>
  <main class="book-cover">
    <div class="cover-photo" role="img" aria-label="Photograph of a blue sky with white clouds and a passenger plane flying overhead, fading into a faint calendar page"></div>
    <div class="figure-area" role="img" aria-label="Photograph of a woman seen from behind with a loose blonde braid and olive tank top, looking up at the sky"></div>

    <div class="title-small">SALT WIND</div>
    <div class="title-feature line-one">OVER THE</div>
    <div class="title-feature line-two">QUIET</div>

    <svg class="date-ring" viewBox="0 0 800 600" aria-hidden="true">
      <ellipse cx="418" cy="268" rx="348" ry="192" transform="rotate(-5 418 268)"
               fill="none" stroke="var(--ring-red)" stroke-width="9" stroke-linecap="round"/>
      <path d="M300 92 C 430 60, 610 62, 700 104" fill="none"
            stroke="var(--ring-red)" stroke-width="7" stroke-linecap="round"/>
    </svg>

    <div class="title-tail">HARBOUR</div>

    <div class="author-name">Lena Dorsk</div>
  </main>
</body>
</html>
```